BuildLinkHub.com Full Stationery Design

Business Card will have all info on it. Letterhead will not have name, title or mobile number. Keep general feeling very clean, using colors from the logo as accents.
Name:Dale Marchetti
Title:President
Phone: 1-800-555-0142
Cell: 306-555-0187
email: dale@buildlinkhub.example
website: www.buildlinkhub.example
Address:
PO Box 947
Larkfield, XA
S0J2T0

Target Market(s)

Construction Business owners

Industry/Entity Type

Business

Contact Information for Business Card

Name:Dale Marchetti
Title:President
Phone: 1-800-555-0142
Cell: 306-555-0187
Address:
PO Box 947
Larkfield, XA
S0J2T0

Font styles to use
Sans Serif

Requirements
Must have
• Clean look
Should not have
• Images or cartoon type characters or tools

```html
<!DOCTYPE html>
<html lang="en">
<head>
<meta charset="utf-8">
<title>BuildLinkHub.com Business Card</title>
<link rel="stylesheet" href="https://fonts.googleapis.com/css2?family=Questrial&family=Noto+Serif:wght@700&family=Roboto:wght@400&display=swap">
<style>
  :root {
    --backdrop: #f7a566;
    --card: #ffffff;
    --ink: #4f5661;
    --ink-soft: #6b717b;
    --accent: #ef5a1c;
    --accent-deep: #e0401a;
    --steel: #8c96a3;
    --rule: #c9cdd2;
  }
  * { box-sizing: border-box; margin: 0; padding: 0; }
  html, body { width: 1200px; height: 856px; overflow: hidden; }
  body {
    background: var(--backdrop);
    display: flex;
    flex-direction: column;
    align-items: center;
    justify-content: center;
    gap: 48px;
    font-family: "Roboto", Arial, sans-serif;
  }
  .card {
    position: relative;
    width: 630px;
    height: 360px;
    background: var(--card);
    border-radius: 28px;
    overflow: hidden;
    box-shadow: 0 10px 24px rgba(150, 70, 10, 0.25);
  }
  .wordmark {
    display: flex;
    align-items: center;
    gap: 14px;
  }
  .wordmark-square {
    width: 40px;
    height: 40px;
    background: var(--accent);
  }
  .wordmark-name {
    font-family: "Questrial", Arial, sans-serif;
    font-size: 40px;
    color: var(--ink);
    letter-spacing: 0.5px;
    white-space: nowrap;
  }
  /* Front side */
  .card-front {
    display: flex;
    align-items: center;
    justify-content: center;
  }
  .edge-tab {
    position: absolute;
    right: 0;
    width: 8px;
  }
  .edge-tab.orange { top: 60px; height: 34px; background: var(--accent); }
  .edge-tab.steel { top: 98px; height: 34px; background: var(--steel); }
  /* Back side */
  .card-back {
    display: flex;
    align-items: center;
    padding: 0 30px 30px 36px;
  }
  .card-back .wordmark { gap: 10px; }
  .card-back .wordmark-square { width: 30px; height: 30px; }
  .card-back .wordmark-name { font-size: 28px; }
  .divider {
    width: 1px;
    height: 120px;
    background: var(--rule);
    margin: 0 22px 0 20px;
    flex: none;
  }
  .contact-name {
    font-family: "Noto Serif", Georgia, serif;
    font-weight: 700;
    font-size: 19px;
    color: var(--accent);
    line-height: 1.1;
  }
  .contact-title {
    font-family: "Noto Serif", Georgia, serif;
    font-weight: 700;
    font-size: 12px;
    color: var(--ink);
    margin-bottom: 6px;
  }
  .contact-list { list-style: none; }
  .contact-list li {
    display: flex;
    align-items: center;
    gap: 8px;
    font-size: 12.5px;
    color: var(--ink-soft);
    line-height: 19px;
    white-space: nowrap;
  }
  .contact-list svg { width: 11px; height: 11px; flex: none; }
  .bottom-band {
    position: absolute;
    bottom: 0;
    left: 0;
    right: 0;
    height: 14px;
    display: flex;
  }
  .bottom-band .orange { flex: 0 0 70%; background: linear-gradient(90deg, var(--accent-deep), var(--accent)); }
  .bottom-band .gap { flex: 0 0 1.5%; background: var(--card); }
  .bottom-band .steel { flex: 1; background: var(--steel); }
</style>
</head>
<body>
  <section class="card card-front">
    <div class="wordmark">
      <span class="wordmark-square"></span>
      <span class="wordmark-name">BuildLinkHub.com</span>
    </div>
    <span class="edge-tab orange"></span>
    <span class="edge-tab steel"></span>
  </section>

  <section class="card card-back">
    <div class="wordmark">
      <span class="wordmark-square"></span>
      <span class="wordmark-name">BuildLinkHub.com</span>
    </div>
    <span class="divider"></span>
    <div class="contact">
      <p class="contact-name">Dale Marchetti</p>
      <p class="contact-title">President</p>
      <ul class="contact-list">
        <li>
          <svg viewBox="0 0 12 12"><path d="M6 0.5a4 4 0 0 1 4 4c0 3-4 7-4 7s-4-4-4-7a4 4 0 0 1 4-4z" fill="var(--accent)"/><circle cx="6" cy="4.5" r="1.5" fill="#fff"/></svg>
          PO Box 947, Larkfield, XA, S0J2T0
        </li>
        <li>
          <svg viewBox="0 0 12 12"><rect x="1" y="3" width="10" height="7" rx="1.5" fill="var(--accent)"/><rect x="3" y="1" width="6" height="3" rx="1" fill="var(--accent)"/></svg>
          1-800-555-0142
        </li>
        <li>
          <svg viewBox="0 0 12 12"><path d="M2.5 1h2l1 3-1.5 1a6 6 0 0 0 3 3l1-1.5 3 1v2a1.5 1.5 0 0 1-1.5 1.5A9 9 0 0 1 1 2.5 1.5 1.5 0 0 1 2.5 1z" fill="var(--accent)"/></svg>
          306-555-0187
        </li>
        <li>
          <svg viewBox="0 0 12 12"><rect x="1" y="2.5" width="10" height="7" rx="1" fill="var(--accent)"/><path d="M1.5 3l4.5 3.5L10.5 3" stroke="#fff" stroke-width="1" fill="none"/></svg>
          dale@buildlinkhub.example
        </li>
        <li>
          <svg viewBox="0 0 12 12"><circle cx="6" cy="6" r="5" fill="var(--accent)"/><path d="M1 6h10M6 1c-2 2.5-2 7.5 0 10M6 1c2 2.5 2 7.5 0 10" stroke="#fff" stroke-width="0.8" fill="none"/></svg>
          www.buildlinkhub.example
        </li>
      </ul>
    </div>
    <div class="bottom-band"><span class="orange"></span><span class="gap"></span><span class="steel"></span></div>
  </section>
</body>
</html>
```